Campaign Website

I need a website for my judicial campaign. I would like a site that directs from this domain as well as a new domain with my married last name. I need separate pages on the site that address my diversion programs, and a page to allow people to donate with a link to my bank account and a link for people to submit requests to volunteer, get yard signs, etc.

```html
<!DOCTYPE html>
<html lang="en">
<head>
<meta charset="utf-8">
<title>Harper Renee — Campaign</title>
<link href="https://fonts.googleapis.com/css2?family=Montserrat:wght@500;600;700;800&family=Raleway:wght@500;600&family=Roboto:wght@400;500;700&display=swap" rel="stylesheet">
<style>
:root{
  --navy:#0a1240;
  --navy-deep:#050b33;
  --blue:#3a87d0;
  --ink:#222;
  --muted:#555;
  --panel:#f4f4f4;
  --slate:#4a4a4a;
  --footer:#141414;
  --link:#2aa3d8;
}
*{margin:0;padding:0;box-sizing:border-box}
html,body{width:1200px;height:4147px;overflow:hidden;background:#fff}
body{position:relative;font-family:'Roboto',sans-serif;color:var(--ink)}
.photo{position:absolute;display:block}
.skew-btn{position:absolute;display:flex;align-items:center;justify-content:center;background:var(--navy-deep);color:#fff;font-family:'Roboto',sans-serif;font-weight:500;text-transform:uppercase;text-decoration:none;clip-path:polygon(8% 0,100% 0,92% 100%,0 100%)}

/* header */
.site-header{position:absolute;left:0;top:0;width:1200px;height:74px}
.brand{position:absolute;left:111px;top:18px;font-family:'Montserrat',sans-serif;font-weight:600;font-size:34px;color:var(--navy);letter-spacing:.5px}
.call{position:absolute;right:111px;top:24px;font-size:17px;color:var(--muted)}
.call b{font-size:22px;color:var(--navy);font-weight:700}
.main-nav{position:absolute;left:0;top:74px;width:1200px;height:44px;background:var(--navy);display:flex;align-items:center;padding-left:154px;gap:51px}
.main-nav a{color:#fff;text-decoration:none;font-family:'Montserrat',sans-serif;font-size:13.5px;font-weight:600;letter-spacing:.3px}
.main-nav a.active{color:#9aa3b8}

/* hero */
.hero-photo{left:0;top:118px;width:1200px;height:567px;background:
  radial-gradient(ellipse 260px 300px at 330px 380px,rgba(150,110,85,.55),transparent 70%),
  radial-gradient(ellipse 240px 280px at 520px 360px,rgba(190,170,150,.4),transparent 70%),
  linear-gradient(90deg,#4a4a58 0%,#5a4a40 30%,#3a3634 58%,#333 100%)}
.hero-curve{position:absolute;left:0;top:570px}
.hero-title{position:absolute;left:652px;top:218px;font-family:'Montserrat',sans-serif;font-weight:800;font-size:74px;line-height:78px;color:#fff;text-shadow:0 2px 8px rgba(0,0,0,.35)}
.hero-donate{left:677px;top:422px;width:161px;height:50px;font-size:20px}

/* about */
.section-title{position:absolute;font-family:'Raleway',sans-serif;font-weight:500;color:var(--ink)}
.about-panel{position:absolute;left:160px;top:826px;width:555px;height:332px;background:var(--panel);padding:20px 0 0 29px;font-size:13px;line-height:26.5px;color:#333}
.about-panel p{width:395px}
.about-panel p+p{margin-top:9px}
.about-more{left:190px;top:1054px;width:141px;height:40px;font-size:14px}
.about-photo{left:640px;top:760px;width:373px;height:366px;background:
  radial-gradient(ellipse 90px 170px at 140px 210px,#e8e4dc,transparent 75%),
  radial-gradient(ellipse 80px 160px at 240px 230px,#5a5a44,transparent 75%),
  linear-gradient(135deg,#4a3426,#6a4a36 55%,#3a2b22);box-shadow:0 10px 30px rgba(0,0,0,.25)}

/* gallery */
.tile{position:absolute;width:400px;height:352px}
.tile-caption{position:absolute;left:38px;bottom:30px;font-family:'Montserrat',sans-serif;font-weight:600;font-size:21px;line-height:28px;color:#fff}
.tile-feature{background:var(--navy-deep);color:#fff;padding:38px 50px 0 37px}
.tile-feature h3{font-family:'Montserrat',sans-serif;font-weight:600;font-size:21px;line-height:28px;margin-bottom:18px}
.tile-feature p{font-size:12.8px;line-height:25.7px;color:#d8dbe8}

/* testimonials */
.map-bg{left:120px;top:2005px;width:960px;height:520px;background:radial-gradient(ellipse at center,rgba(0,0,0,.035) 0%,rgba(0,0,0,.02) 50%,rgba(0,0,0,0) 72%)}
.quote-mark{position:absolute;left:157px;top:2150px;font-family:Georgia,serif;font-size:34px;color:#555;letter-spacing:-3px}
.quote-text{position:absolute;left:188px;top:2157px;width:815px;font-size:13px;line-height:28px;color:#444}
.avatar{left:158px;top:2263px;width:101px;height:102px;border-radius:50%;background:radial-gradient(circle at 45% 45%,#c9a5a7,#7a5a6a)}
.reviewer{position:absolute;left:281px;top:2275px;font-size:12px;line-height:25px;color:#333}
.reviewer em{font-family:Georgia,serif;font-size:12.5px}
.reviewer a{color:var(--link);text-decoration:none}
.reviews-btn{left:833px;top:2294px;width:175px;height:40px;font-size:13px}

/* events */
.ev-box{position:absolute;color:#fff;padding:48px 28px 0 28px}
.ev-box h3{font-family:'Montserrat',sans-serif;font-weight:600;font-size:21px;line-height:28px;margin-bottom:18px}
.ev-box p{font-size:13px;line-height:22px;margin-bottom:16px;width:320px}
.ev-box u{text-underline-offset:2px}
.ev-box .view-all{font-size:11.5px;text-decoration:underline;color:#d8dbe8}
.ev-date{position:absolute;left:26px;bottom:16px;font-family:'Montserrat',sans-serif;font-weight:600;font-size:21px;color:#fff}
.play{position:absolute;left:50%;top:50%;transform:translate(-50%,-50%)}

/* contact */
.contact-name{position:absolute;left:155px;top:3688px;font-family:'Montserrat',sans-serif;font-weight:600;font-size:34px;line-height:40px;color:var(--navy)}
.field{position:absolute;left:499px;width:539px;height:46px;border:1px solid #dcdcdc;font-size:14px;color:#555;padding:14px 27px}
.submit-btn{left:491px;top:3878px;width:190px;height:48px;font-size:15px}

/* footer */
.site-footer{position:absolute;left:0;top:4022px;width:1200px;height:125px;background:var(--footer)}
.copyright{position:absolute;left:112px;top:56px;font-size:12.5px;color:#fff}
.social{position:absolute;right:111px;top:56px;display:flex;gap:34px}
.social span{width:14px;height:14px;border-radius:50%;background:#fff;display:block}
</style>
</head>
<body>

<header class="site-header">
  <div class="brand">HARPER RENEE</div>
  <div class="call">Call Us : <b>(555) 304-7182</b></div>
</header>
<nav class="main-nav">
  <a class="active" href="#">HOME</a>
  <a href="#">BIOGRAPHY</a>
  <a href="#">EVENTS</a>
  <a href="#">ENDORSEMENTS</a>
  <a href="#">VOTING INFORMATION</a>
  <a href="#">DONATE</a>
  <a href="#">CONTACT</a>
</nav>

<section class="hero">
  <div class="photo hero-photo" role="img" aria-label="Photo of the candidate smiling with a supporter at a campaign gathering"></div>
  <svg class="hero-curve" width="1200" height="120" viewBox="0 0 1200 120">
    <path d="M0 115 L600 16 L1200 115 L1200 120 L0 120 Z" fill="#fff"/>
    <path d="M0 115 L600 16 L1200 115" fill="none" stroke="var(--blue)" stroke-width="6"/>
  </svg>
  <h1 class="hero-title">HARPER<br>RENEE</h1>
  <a class="skew-btn hero-donate">DONATE</a>
</section>

<section class="about">
  <h2 class="section-title" style="left:160px;top:750px;font-size:38px">About Me</h2>
  <div class="about-panel">
    <p>My candidacy is based on the belief that the judiciary needs to be accountable to the citizens it serves. This starts with being present and accessible to ensure that both victims of crime, as well as those accused, have their day in court without unnecessary delays.</p>
    <p>Additionally, it is incumbent upon the judiciary to be proactive and innovative by starting programs that work...</p>
  </div>
  <a class="skew-btn about-more">READ MORE</a>
  <div class="photo about-photo" role="img" aria-label="Portrait of the candidate with her husband"></div>
</section>

<section class="gallery">
  <div class="tile" style="left:0;top:1261px;background:linear-gradient(180deg,#8a7f70 0%,#4a4058 45%,#2a2a35 100%)" role="img" aria-label="Photo of the candidate with sorority members">
    <div class="tile-caption">Sed ut perspiciatis unde<br>omnis iste natus</div></div>
  <div class="tile tile-feature" style="left:400px;top:1261px">
    <h3>Sed ut perspiciatis unde<br>omnis iste natus</h3>
    <p>Sed ut perspiciatis unde omnis iste natus error sit voluptatem accusantium doloremque laudantium, totam rem aperiam, eaque ipsa quæ ab illo tore veritatis et quasi architecto beatæ vitæ dicta sunt explicab<br>ntium doloremque laudantium, totam rem aperiam, eaque ipsa quæ ab illo tore veritatis et quasi archi-tecto beatæ vitæ dicta sunt explicab</p>
  </div>
  <div class="tile" style="left:800px;top:1261px;background:linear-gradient(180deg,#e8e4e0 0%,#8a7a74 40%,#3a3236 100%)" role="img" aria-label="Photo of the candidate with students at a school event">
    <div class="tile-caption">Sed ut perspiciatis unde<br>omnis iste natus</div></div>
  <div class="tile" style="left:0;top:1613px;background:linear-gradient(100deg,#6a4a3a 0%,#4a5a4a 45%,#2a3a8a 70%,#2a3070 100%)" role="img" aria-label="Photo of the candidate with a supporter">
    <div class="tile-caption">Sed ut perspiciatis unde<br>omnis iste natus</div></div>
  <div class="tile" style="left:400px;top:1613px;background:linear-gradient(180deg,#e0e0e0 0%,#9a9a9a 35%,#3a3a3a 100%)" role="img" aria-label="Photo of the candidate with law students at a banner">
    <div class="tile-caption">Sed ut perspiciatis unde<br>omnis iste natus</div></div>
  <div class="tile" style="left:800px;top:1613px;background:linear-gradient(160deg,#d0602a 0%,#8a3a2a 50%,#3a2a2a 100%)" role="img" aria-label="Photo of the candidate with family and friends">
    <div class="tile-caption">Sed ut perspiciatis unde<br>omnis iste natus</div></div>
</section>

<section class="testimonials">
  <div class="photo map-bg" role="img" aria-label="Faint world map background"></div>
  <h2 class="section-title" style="left:0;width:1200px;text-align:center;top:2075px;font-size:38px">Testimonials</h2>
  <div class="quote-mark">66</div>
  <p class="quote-text">Lorem ipsum dolor sit amet, consectetur adipiscing elit, sed do eiusmod tempor incididunt ut labore et dolore magna aliqua. Ut enim<br>ad minim veniam, quis nostrud exercitation ullamco laboris nisi ut aliquip ex ea commodo consequat. Duis aute irure dolor in<br>reprehenderit in voluptate velit esse cillum dolore eu fugiat nulla pariatur</p>
  <div class="photo avatar" role="img" aria-label="Reviewer portrait"></div>
  <div class="reviewer">Dan Whitford, Chief Operations &amp; Growth Officer, Global<br><em>2 June</em><br><a href="#">Sed ut perspiciatis unde</a></div>
  <a class="skew-btn reviews-btn">SEE MORE REVIEWS</a>
</section>

<section class="events">
  <h2 class="section-title" style="left:0;width:1200px;text-align:center;top:2455px;font-size:38px">Events</h2>

  <div class="photo" style="left:111px;top:2539px;width:274px;height:356px;background:linear-gradient(180deg,#d0ccc4 0%,#7a6a60 45%,#2a2a2a 100%)" role="img" aria-label="Photo of the candidate greeting a judge in a courtroom">
    <span class="ev-date">April 2018</span></div>
  <div class="ev-box" style="left:395px;top:2539px;width:404px;height:285px;background:var(--navy-deep)">
    <h3>Articles</h3>
    <p>Sed ut perspiciatis unde omnis iste natus error sit voluptatem<u>(featured in March 2018 article)</u></p>
    <p>Sed ut perspiciatis unde omnis iste natus error sit voluptatem<u>(featured in March 2018 article)</u></p>
    <span class="view-all">VIEW ALL</span>
  </div>
  <div class="photo" style="left:807px;top:2539px;width:281px;height:285px;background:linear-gradient(170deg,#8aa06a 0%,#c04040 45%,#3a2a2a 100%)" role="img" aria-label="Photo of the candidate with a supporter at an outdoor event">
    <span class="ev-date">March 2018</span></div>

  <div class="photo" style="left:111px;top:2905px;width:274px;height:245px;background:linear-gradient(180deg,#e0a878 0%,#6a4030 55%,#2a2a2a 100%)" role="img" aria-label="Photo of the candidate holding donated toys"></div>
  <div class="photo" style="left:395px;top:2834px;width:320px;height:316px;background:linear-gradient(135deg,#3a2a24,#8a5a44 50%,#2a1e1a)" role="img" aria-label="Photo of the candidate with a friend"></div>
  <div class="ev-box" style="left:725px;top:2834px;width:363px;height:316px;background:var(--slate)">
    <h3>Sed ut perspiciatis<br>unde omnis iste<br>natus</h3>
    <p>Sed ut perspiciatis unde omnis iste natus error sit voluptatem<u>(featured in March 2018 article)</u></p>
    <span class="view-all">VIEW ALL</span>
  </div>

  <div class="photo" style="left:111px;top:3159px;width:480px;height:290px;background:linear-gradient(180deg,#8a9ab0 0%,#9a3030 50%,#3a1a1a 100%)" role="img" aria-label="Video thumbnail of a gift drive with volunteers">
    <svg class="play" width="26" height="30" viewBox="0 0 26 30"><path d="M0 0 L26 15 L0 30 Z" fill="#fff"/></svg></div>
  <div class="photo" style="left:599px;top:3159px;width:489px;height:290px;background:linear-gradient(180deg,#9a8a7a 0%,#4a3a34 45%,#c8c0b4 100%)" role="img" aria-label="Video thumbnail of students at an assembly">
    <svg class="play" width="26" height="30" viewBox="0 0 26 30"><path d="M0 0 L26 15 L0 30 Z" fill="#fff"/></svg></div>
</section>

<section class="contact">
  <h2 class="section-title" style="left:155px;top:3588px;font-size:38px">Contact Us</h2>
  <div class="contact-name">HARPER<br>RENEE</div>
  <div class="field" style="top:3586px">Name</div>
  <div class="field" style="top:3644px">Email</div>
  <div class="field" style="top:3700px">Subject</div>
  <div class="field" style="top:3758px;height:89px">Message</div>
  <a class="skew-btn submit-btn">SUBMIT</a>
</section>

<footer class="site-footer">
  <div class="copyright">2019 Copyrights.All Rights Reserved</div>
  <div class="social">
    <span aria-label="Professional network"></span><span aria-label="Microblog"></span><span aria-label="Social page"></span><span aria-label="Photo feed"></span>
  </div>
</footer>

</body>
</html>
```